Design and Renovation Company Luxury Business Card

I want to create a luxury business card for a Design and Renovation Firm . We will use our current logo. The company name is 528BUILDA. We do not want anything standard. We need a very unique concept.
Please see uploaded inspiration. I really like the textured paper option. I would like the card to be thick with debossing, and/or embossing options. The logo has orange in it but I would like to see the card with and without the orange. I think the orange may make the company feel less high-end. The goal is to elevate the logo not match its vibe per se of the logo. We want something very unique, not standard at all!
I would like a space for :
Logo,
Name,
Position,
Email,
Office number,
Website Address,
Business Address,
Thank you!
Have fun!
Target Market(s)
Home owners Age 35 +
Industry/Entity Type
Design and Renovation
Contact Information for Business Card
Logo, Name, Position, Email, Office number, Website Address, Business Address,.
Colors
Designer to choose colors to be used in the design.
Requirements
Must have
- A luxury designer feel. Must be black or dark grey but open to other luxury ideas.
Nice to have
- Gold, silver, black embossing or debossing. Textured paper design.
Should not have
- A cheap look and feel.

```html
<!DOCTYPE html>
<html lang="en">
<head>
<meta charset="utf-8">
<title>528BUILDA Business Card</title>
<link rel="stylesheet" href="https://fonts.googleapis.com/css2?family=Open+Sans:wght@400;500&display=swap">
<style>
  :root {
    --ink: #030303;
    --paper: #ffffff;
    --accent: #f7941d;
    --stage: #a8a8a8;
    --rule: #8c8c8c;
  }
  * { margin: 0; padding: 0; box-sizing: border-box; }
  html, body { width: 1136px; height: 1200px; overflow: hidden; background: var(--stage); }
  body { position: relative; font-family: "Open Sans", Arial, sans-serif; }

  .card {
    position: absolute;
    left: 118px;
    width: 900px;
    height: 513px;
    background: var(--ink);
    overflow: hidden;
  }
  .card--front { top: 58px; }
  .card--back { top: 629px; }

  .card__edges { position: absolute; inset: 0; width: 900px; height: 513px; }

  .brand { position: absolute; display: flex; align-items: flex-end; color: var(--paper); font-weight: 500; white-space: nowrap; }
  .brand__square { background: var(--accent); flex: none; }

  .card--front .brand { left: 0; right: 0; top: 206px; justify-content: center; gap: 16px; font-size: 74px; line-height: 1; letter-spacing: 3px; }
  .card--front .brand__square { width: 52px; height: 52px; margin-bottom: 8px; }

  .card--back .brand { left: 42px; top: 50px; gap: 8px; font-size: 32px; line-height: 1; letter-spacing: 1px; }
  .card--back .brand__square { width: 24px; height: 24px; margin-bottom: 3px; }

  .person { position: absolute; right: 67px; top: 56px; text-align: right; }
  .person__company { color: var(--paper); font-size: 34px; line-height: 42px; font-weight: 500; }
  .person__line { color: var(--accent); font-size: 24px; line-height: 34px; }
  .person__role { color: var(--accent); font-size: 20px; line-height: 30px; }
  .person__icon { position: absolute; right: -30px; top: 14px; }

  .contact { position: absolute; list-style: none; font-size: 21px; line-height: 32px; color: var(--paper); }
  .contact li { display: flex; align-items: center; gap: 14px; }
  .contact--local { left: 42px; top: 292px; }
  .contact--online { right: 34px; top: 398px; text-align: right; }
  .contact--online li { justify-content: flex-end; }
  .dot { width: 12px; height: 12px; flex: none; }

  .rule { position: absolute; left: 42px; top: 373px; width: 481px; height: 2px; background: var(--rule); }
</style>
</head>
<body>

<section class="card card--front" aria-label="Business card front">
  <svg class="card__edges" viewBox="0 0 900 513" aria-hidden="true">
    <rect x="0" y="0" width="446" height="5" fill="var(--accent)"/>
    <path d="M444 0 H900 V22 H458 A14 14 0 0 1 444 8 Z" fill="var(--paper)"/>
    <path d="M0 491 H440 A14 14 0 0 1 454 505 V513 H0 Z" fill="var(--accent)"/>
    <rect x="454" y="509" width="446" height="4" fill="var(--paper)"/>
  </svg>
  <div class="brand"><span class="brand__square"></span><span class="brand__name">528BUILDA</span></div>
</section>

<section class="card card--back" aria-label="Business card back">
  <svg class="card__edges" viewBox="0 0 900 513" aria-hidden="true">
    <rect x="0" y="0" width="446" height="5" fill="var(--accent)"/>
    <path d="M444 0 H900 V22 H458 A14 14 0 0 1 444 8 Z" fill="var(--paper)"/>
    <path d="M0 491 H440 A14 14 0 0 1 454 505 V513 H0 Z" fill="var(--accent)"/>
    <rect x="454" y="509" width="446" height="4" fill="var(--paper)"/>
  </svg>

  <div class="brand"><span class="brand__square"></span><span class="brand__name">528BUILDA</span></div>

  <div class="person">
    <p class="person__company">528BUILDA Design</p>
    <p class="person__line">and renovation firm</p>
    <p class="person__role">Ceo</p>
    <svg class="person__icon dot" viewBox="0 0 12 12" aria-hidden="true">
      <circle cx="6" cy="6" r="6" fill="var(--paper)"/>
      <circle cx="6" cy="4.5" r="1.8" fill="var(--ink)"/>
      <path d="M2.8 9.6 A3.2 3 0 0 1 9.2 9.6 Z" fill="var(--ink)"/>
    </svg>
  </div>

  <ul class="contact contact--local">
    <li>
      <svg class="dot" viewBox="0 0 12 12" aria-hidden="true"><circle cx="6" cy="6" r="6" fill="var(--paper)"/><circle cx="6" cy="6" r="2.4" fill="var(--ink)"/></svg>
      <span>+ 1234567890</span>
    </li>
    <li>
      <svg class="dot" viewBox="0 0 12 12" aria-hidden="true"><circle cx="6" cy="6" r="6" fill="var(--paper)"/><circle cx="6" cy="6" r="2.4" fill="var(--ink)"/></svg>
      <span>Dummy City, Dummy Country</span>
    </li>
  </ul>

  <div class="rule"></div>

  <ul class="contact contact--online">
    <li>
      <span>info@528buildadesign and renovation firm.com</span>
      <svg class="dot" viewBox="0 0 12 12" aria-hidden="true"><circle cx="6" cy="6" r="6" fill="var(--paper)"/><circle cx="6" cy="6" r="2.4" fill="var(--ink)"/></svg>
    </li>
    <li>
      <span>www.528buildadesign and renovation firm.com</span>
      <svg class="dot" viewBox="0 0 12 12" aria-hidden="true"><circle cx="6" cy="6" r="6" fill="var(--paper)"/><circle cx="6" cy="6" r="2.4" fill="var(--ink)"/></svg>
    </li>
  </ul>
</section>

</body>
</html>
```